New Pump Website Design Needed

We need a homepage concept for a pump website rebuild.

The navigation at the top must be:
Home - About Us - Pump Stations - Pumps - Electrical - Drainage - Environmental - Accessories - Contact Us

The homepage should have the the following structure:
Logo
Navigation
Rotating Banner
Content + Picture of PDF Flipbook to download/ view
Featured Products (in one row - approx 4)
Footer

The footer must include:
Left side - navigation small.
"Copyright KelvoRun 2014. All Rights reserved"

Right side: "Website by Pixel Orchard Studio"

Content and imagery, and Logo can be taken from their existing website: tarnbrookvalves.co.nz

We have attached a copy of their New PDF - the new website design must reflect this (Use block colours/ different colours for the navigation items/ incorporate the footer image).

Industry/Entity Type

Electrical

Font styles to use
Sans Serif

Requirements
Must have
• Features from their brochure brought in (colour scheme and footer feature)
Should not have
• Any Social Media Icons

```html
<!DOCTYPE html>
<html lang="en">
<head>
<meta charset="utf-8">
<title>KelvoRun Pump Systems</title>
<link href="https://fonts.googleapis.com/css2?family=Michroma&family=Open+Sans:wght@400;600&family=Arimo:wght@400;700&display=swap" rel="stylesheet">
<style>
  :root {
    --blue: #2a83c6;
    --blue-dark: #0e5aa0;
    --green: #6cb33f;
    --green-bright: #9ddc1f;
    --ink: #1a1a1a;
    --text: #444;
    --panel: #1f1f1f;
    --footer: #231f20;
  }
  * { margin: 0; padding: 0; box-sizing: border-box; }
  html, body { width: 1163px; height: 1200px; overflow: hidden; background: #fff; }
  body { position: relative; font-family: "Arimo", Arial, sans-serif; color: var(--text); }
  .abs { position: absolute; }

  /* Header */
  .brand { left: 96px; top: 34px; display: flex; align-items: center; gap: 12px; }
  .brand-mark { width: 34px; height: 34px; background: var(--blue-dark); }
  .brand-name { font-family: "Arimo", sans-serif; font-weight: 700; font-size: 38px; color: var(--blue-dark); letter-spacing: 1px; }
  .search-label { left: 738px; top: 36px; display: flex; align-items: center; gap: 8px; font-weight: 700; font-size: 12px; color: #5d9c3c; }
  .search-box { left: 842px; top: 31px; width: 222px; height: 32px; border-radius: 16px; border: 2px solid #d8d8d8;
    background: linear-gradient(#f6f6f6, #e9e9e9); }
  .search-box svg { position: absolute; right: 10px; top: 5px; }
  .nav { left: 384px; top: 82px; width: 682px; height: 44px; }
  .nav-bg { position: absolute; inset: 0; }
  .nav-list { position: absolute; left: 30px; right: 8px; top: 0; height: 44px; display: flex; align-items: center;
    justify-content: space-between; list-style: none; font-size: 12px; color: #fff; white-space: nowrap; }
  .nav-list li { display: flex; align-items: center; }
  .nav-list li + li::before { content: "|"; margin-right: 6px; }
  .rule { left: 0; top: 126px; width: 1163px; height: 5px; background: var(--blue-dark); }

  /* Hero */
  .hero { left: 0; top: 131px; width: 1163px; height: 442px;
    background: radial-gradient(ellipse at 50% 40%, #5a5a5a 0%, #3d3d3d 55%, #2c2c2c 100%); }
  .hero-frame { left: 118px; top: 170px; width: 640px; height: 403px; background: #111; border-radius: 4px; }
  .hero-photo { left: 127px; top: 179px; width: 626px; height: 386px;
    background: linear-gradient(180deg, #c9d6c4 0%, #7a9a58 38%, #6a7d43 55%, #6b4a32 80%, #4f3a2a 100%); }
  .ribbon { left: 116px; top: 167px; }
  .flip-panel { left: 755px; top: 161px; width: 288px; height: 412px; background: var(--panel);
    border: 6px solid #2b2b2b; border-bottom: none; }
  .flip-title { left: 775px; top: 202px; font-family: "Michroma", sans-serif; font-size: 16px; color: #fff; white-space: nowrap; }
  .flip-title span { color: var(--blue); }
  .flip-list { left: 782px; top: 244px; width: 215px; list-style: none; font-family: "Open Sans", sans-serif;
    font-size: 11px; line-height: 15.5px; color: #fff; }
  .flip-list li { position: relative; padding-left: 15px; margin-bottom: 14px; }
  .flip-list li::before { content: ""; position: absolute; left: 0; top: 4px; border-left: 5px solid #fff;
    border-top: 4px solid transparent; border-bottom: 4px solid transparent; }
  .btn-download { left: 784px; top: 527px; width: 135px; height: 25px; background: var(--green); color: #fff;
    font-size: 13px; display: flex; align-items: center; justify-content: center; border-radius: 2px; }

  /* Welcome */
  .welcome-title { left: 102px; top: 612px; font-family: "Michroma", sans-serif; font-size: 19px;
    color: var(--ink); -webkit-text-stroke: .4px var(--ink); white-space: nowrap; }
  .welcome-copy { left: 107px; top: 656px; width: 950px; font-size: 13px; line-height: 21.5px; color: var(--text);
    text-align: justify; }
  .welcome-copy strong { color: var(--green); font-weight: 700; }

  /* Cards */
  .card { top: 797px; width: 226px; height: 249px; border: 1px solid #ddd; border-top: none;
    background: linear-gradient(#fff 0%, #fff 35%, #e6e6e6 100%); }
  .card-head { height: 32px; background: linear-gradient(var(--blue) 0%, var(--blue-dark) 100%); color: #fff;
    font-family: "Michroma", sans-serif; font-size: 12.5px; display: flex; align-items: center; justify-content: center; white-space: nowrap; }
  .card-photo { position: absolute; left: 18px; top: 48px; width: 189px; height: 85px; }
  .photo-a { background: linear-gradient(135deg, #8aa0a8, #2d63b7 55%, #5a6d78); }
  .photo-b { background: linear-gradient(135deg, #a8a092, #3a5b9e 50%, #bdb3a0); }
  .photo-c { background: linear-gradient(160deg, #a6a99a, #6f6a4f 50%, #8c7a55); }
  .photo-d { background: linear-gradient(150deg, #9fb0b8, #4a6f8f 50%, #7d8a80); }
  .card-text { position: absolute; left: 10px; top: 148px; width: 204px; text-align: center; font-size: 12.5px;
    line-height: 18px; color: #333; }
  .card-btn { position: absolute; left: 55px; top: 227px; width: 115px; height: 33px; border-radius: 3px;
    background: linear-gradient(#8f8f8f, #5e5e5e); color: #fff; font-size: 17px;
    display: flex; align-items: center; justify-content: center; box-shadow: 0 3px 5px rgba(0,0,0,.3); }

  /* Footer */
  .footer-line { left: 0; top: 1098px; width: 1163px; height: 4px; background: var(--green); }
  .footer { left: 0; top: 1102px; width: 1163px; height: 98px; background: var(--footer); }
  .footer-nav { left: 97px; top: 1129px; list-style: none; display: flex; font-size: 14px; color: #d7d7d7; letter-spacing: .3px; }
  .footer-nav li + li::before { content: "|"; margin: 0 9px; }
  .copyright { left: 97px; top: 1153px; font-size: 12px; color: #e6e6e6; }
  .footer-brand { left: 840px; top: 1097px; width: 226px; height: 72px; background: #fff;
    display: flex; align-items: center; justify-content: center; gap: 9px; }
  .footer-brand .brand-mark { width: 20px; height: 20px; }
  .footer-brand .brand-name { font-size: 26px; }
  .credit { left: 840px; top: 1177px; width: 226px; text-align: right; font-size: 12px; color: #e6e6e6; }
</style>
</head>
<body>
  <header>
    <div class="abs brand">
      <span class="brand-mark"></span>
      <span class="brand-name">KELVORUN</span>
    </div>
    <div class="abs search-label">
      <svg width="40" height="22" viewBox="0 0 40 22" aria-hidden="true"><circle cx="20" cy="11" r="9" fill="#777"/></svg>
      Search
    </div>
    <div class="abs search-box">
      <svg width="18" height="18" viewBox="0 0 18 18" aria-hidden="true">
        <circle cx="7" cy="7" r="5" fill="none" stroke="#333" stroke-width="1.6"/>
        <line x1="11" y1="11" x2="16" y2="16" stroke="#333" stroke-width="2.4" stroke-linecap="round"/>
      </svg>
    </div>
    <nav class="abs nav">
      <svg class="nav-bg" width="682" height="44" viewBox="0 0 682 44" aria-hidden="true">
        <polygon points="24,0 682,0 682,44 0,44" fill="var(--blue)"/>
      </svg>
      <ul class="nav-list">
        <li>Home</li><li>About Us</li><li>Pump Stations</li><li>Pumps</li><li>Electrical</li><li>Drainage</li><li>Environmental</li><li>Accessories</li><li>Contact Us</li>
      </ul>
    </nav>
    <div class="abs rule"></div>
  </header>

  <section class="hero-area">
    <div class="abs hero"></div>
    <div class="abs hero-frame"></div>
    <div class="abs hero-photo" role="img" aria-label="Compact track loader digging a trench for a pipeline beside a house"></div>
    <svg class="abs ribbon" width="96" height="84" viewBox="0 0 96 84" aria-label="Featured">
      <polygon points="62,0 92,0 4,82 0,52" fill="var(--green-bright)"/>
      <text x="38" y="42" transform="rotate(-42 38 42)" font-family="Arimo, sans-serif" font-size="11" fill="#fff" text-anchor="middle">Featured</text>
    </svg>
    <div class="abs flip-panel"></div>
    <h2 class="abs flip-title">View <span>ONLINE FLIPBOK</span></h2>
    <ul class="abs flip-list">
      <li>Cement &amp; Aggregate Consulting Adds a New E-Band Gigabit Radio</li>
      <li>Cement &amp; Aggregate Consulting-MPLS with its Veltrane Microwave Radios</li>
      <li>Cement &amp; Aggregate Consulting-Veltrane MX12 Microwave Radio</li>
      <li>Cement &amp; Aggregate Consulting a New VAR Program</li>
      <li>Cement &amp; Aggregate Consulting a New VAR Program</li>
      <li>Cement &amp; Aggregate Consulting a New VAR Program</li>
    </ul>
    <div class="abs btn-download">Download Here</div>
  </section>

  <section class="welcome">
    <h1 class="abs welcome-title">Welcome to Tarnbrook Pumps.</h1>
    <p class="abs welcome-copy"><strong>simply dummy text of the printing and typesetting industry.</strong> Lorem Ipsum has been the industry's standard dummy text ever since the 1500s, when an unknown printer took a galley of type and scrambled it to make a type specimen book. It has survived not only five centuries, but also the leap into electronic typesetting, remaining essentially unchanged. It was popularised in the 1960s with the release of Dryprint sheets containing Lorem Ipsum passages, and more recently with desktop publishing software like Quillset Layout including versions of Lorem Ipsum.</p>
  </section>

  <section class="cards">
    <article class="abs card" style="left:96px">
      <div class="card-head">Products &amp; Services</div>
      <div class="card-photo photo-a" role="img" aria-label="Workers installing a large blue pipe valve in a pit"></div>
      <p class="card-text">Discover our innovative and comprehensive line of licensed microwave radios and full turnkey services.</p>
      <div class="card-btn">Read More</div>
    </article>
    <article class="abs card" style="left:344px">
      <div class="card-head">Industries Products</div>
      <div class="card-photo photo-b" role="img" aria-label="Worker assembling a long blue pump shaft on site"></div>
      <p class="card-text">Discover our innovative and comprehensive line of licensed microwave radios and full turnkey services.</p>
      <div class="card-btn">Read More</div>
    </article>
    <article class="abs card" style="left:592px">
      <div class="card-head">Pump Stations</div>
      <div class="card-photo photo-d" role="img" aria-label="Pump station installation with pipework"></div>
      <p class="card-text">Discover our innovative and comprehensive line of licensed microwave radios and full turnkey services.</p>
      <div class="card-btn">Read More</div>
    </article>
    <article class="abs card" style="left:840px">
      <div class="card-head">Get Support</div>
      <div class="card-photo photo-c" role="img" aria-label="Excavator working on a muddy construction site"></div>
      <p class="card-text">Discover our innovative and comprehensive line of licensed microwave radios and full turnkey services.</p>
      <div class="card-btn">Read More</div>
    </article>
  </section>

  <footer>
    <div class="abs footer-line"></div>
    <div class="abs footer"></div>
    <ul class="abs footer-nav">
      <li>Home</li><li>Pump</li><li>Station</li><li>Pump</li><li>Electrical</li><li>Drainage</li><li>Environmental</li><li>Accessories</li>
    </ul>
    <p class="abs copyright">Copyright KelvoRun 2014. All Rights reserved</p>
    <div class="abs footer-brand">
      <span class="brand-mark"></span>
      <span class="brand-name">KELVORUN</span>
    </div>
    <p class="abs credit">Website by Pixel Orchard Studio</p>
  </footer>
</body>
</html>
```